Sticker olive oil

Good day,
I would like to design a sticker that will be stuck on an olive oil bottle. It should have the manufacturer's picture on it (in the background, as a hologram, ....?). The brand is a made-up word, composed of the name of the producer "Berello" and the Italian "Olio" for oil. So composed: BerellOlio; the double "O" in the middle could be represented as an olive, then there is an immediate reference to the olive oil. Other textual content should be:
Main brand: "BerellOlio"
Description: "cold pressed, pure olive oil from the Valle - Dursa (Cambella)
Addition: "guaranteed untreated"
You can reach me via my email info@korvandt.de
Payment via PayPal; budget 50 €
I'm still trying to upload the current label, the picture of Berello too

Logo Text

BerellOlio

```html
<!DOCTYPE html>
<html lang="en">
<head>
<meta charset="utf-8">
<title>BerellOlio – Bottle Label</title>
<link rel="stylesheet" href="https://fonts.googleapis.com/css2?family=Josefin+Sans:wght@600;700&display=swap">
<style>
  :root {
    --backdrop: #0d0c0b;
    --paper: #f3f1ea;
    --paper-edge: #e2ded2;
    --ink: #151412;
    --olive: #5c5a2c;
    --gold: #c89a2e;
    --portrait-a: #e6e5cc;
    --portrait-b: #d6d6ad;
  }
  html, body {
    margin: 0;
    padding: 0;
    width: 920px;
    height: 1200px;
    overflow: hidden;
    background: var(--backdrop);
  }
  .canvas {
    position: relative;
    width: 920px;
    height: 1200px;
    font-family: "Josefin Sans", "Helvetica Neue", sans-serif;
  }
  .label-shape {
    position: absolute;
    inset: 0;
  }
  .portrait {
    position: absolute;
    left: 300px;
    top: 150px;
    width: 320px;
    height: 350px;
    border-radius: 46% 46% 38% 38% / 42% 42% 30% 30%;
    background: radial-gradient(ellipse at 50% 40%, var(--portrait-b) 0%, var(--portrait-a) 55%, rgba(243,241,234,0) 80%);
  }
  .brand {
    position: absolute;
    left: 0;
    width: 920px;
    top: 530px;
    text-align: center;
    font-weight: 700;
    font-size: 92px;
    letter-spacing: 2px;
    text-transform: uppercase;
    color: var(--ink);
    line-height: 1;
  }
  .descriptor {
    position: absolute;
    left: 0;
    width: 920px;
    text-align: center;
    font-weight: 600;
    text-transform: uppercase;
    line-height: 1;
  }
  .descriptor--method { top: 660px; font-size: 32px; letter-spacing: 3px; color: var(--olive); }
  .descriptor--product { top: 720px; font-size: 36px; letter-spacing: 4px; color: var(--gold); }
  .descriptor--origin { top: 786px; font-size: 26px; letter-spacing: 3px; color: var(--olive); }
  .descriptor--place { top: 826px; font-size: 26px; letter-spacing: 3px; color: var(--olive); }
  .rule {
    position: absolute;
    top: 738px;
    width: 80px;
    height: 2px;
    background: var(--gold);
  }
  .rule--left { left: 120px; }
  .rule--right { right: 120px; }
  .promise-dot {
    position: absolute;
    left: 435px;
    top: 910px;
    width: 50px;
    height: 50px;
    border-radius: 50%;
    background: var(--gold);
  }
  .promise {
    position: absolute;
    left: 0;
    width: 920px;
    top: 985px;
    text-align: center;
    font-weight: 600;
    font-size: 24px;
    letter-spacing: 4px;
    text-transform: uppercase;
    color: var(--olive);
    line-height: 1;
  }
</style>
</head>
<body>
<div class="canvas">
  <svg class="label-shape" width="920" height="1200" viewBox="0 0 920 1200" aria-hidden="true">
    <path d="M460 40 C640 60 840 180 850 420 L850 820 C840 980 620 1100 460 1160 C300 1100 80 980 70 820 L70 420 C80 180 280 60 460 40 Z"
          fill="var(--paper)" stroke="var(--paper-edge)" stroke-width="4"/>
    <path d="M460 70 C625 90 815 200 822 425 L822 815 C812 960 610 1070 460 1128 C310 1070 108 960 98 815 L98 425 C105 200 295 90 460 70 Z"
          fill="none" stroke="var(--gold)" stroke-width="2"/>
  </svg>

  <div class="portrait" role="img" aria-label="Faint engraved-style portrait of the olive oil producer"></div>

  <div class="brand">BerellOlio</div>

  <div class="descriptor descriptor--method">Cold Pressed</div>
  <span class="rule rule--left"></span>
  <div class="descriptor descriptor--product">Pure Olive Oil</div>
  <span class="rule rule--right"></span>
  <div class="descriptor descriptor--origin">From the Valle Dursa</div>
  <div class="descriptor descriptor--place">-Cambella-</div>

  <span class="promise-dot"></span>
  <div class="promise">Guaranteed untreated</div>
</div>
</body>
</html>
```